Design a website for a newly developed Delta 8 THC Company

Design a responsive Website with the following goals in mind:
- Built on Wordpress/WooCommerce theme. Please use this when designing for ease of integration.
- Build trust with website visitors with an engaging, informative content driven website, that leads to a conversion of product purchase and repeat business. We will also be driving consumers to businesses that carry our products as well.
- The website will embody a lifestyle feel and make the visitor identify with the content.
- The website will allow for super charged SEO and other digital marketing and advertising strategies and tactics used to increase discovery, awareness, and conversion.
Please see additional goals in the uploaded files.
Target Market(s)
Male/Female 21-
Industry/Entity Type
Cannabis/Hemp
Coding
Coded - Design and coding required
Number of Pages Required
5+ page
Font styles to use
Other font styles liked:
- Montserrat
Look and feel
Each slider illustrates characteristics of the customer's brand and the style your logo design should communicate.

```html
<!DOCTYPE html>
<html lang="en">
<head>
<meta charset="utf-8">
<title>Halcyon – Our Story</title>
<link href="https://fonts.googleapis.com/css2?family=Playfair+Display:wght@700;900&family=Poppins:wght@400;500;600&display=swap" rel="stylesheet">
<style>
:root{
  --gold:#c29a3a;
  --gold-light:#f5ec6e;
  --gold-mid:#e2c75a;
  --ink:#1b1b1b;
  --text:#555;
  --soft:#f7f7f7;
  --footer:#3d3d3f;
  --white:#fff;
}
*{margin:0;padding:0;box-sizing:border-box}
html,body{width:1200px;height:2576px;overflow:hidden}
body{position:relative;font-family:"Poppins",sans-serif;color:var(--ink);background:var(--white)}
.abs{position:absolute}
.serif{font-family:"Playfair Display",serif;font-weight:700}

.promo-bar{left:0;top:0;width:1200px;height:31px;background:linear-gradient(90deg,#ecd97a,var(--gold));font-size:12px;font-weight:500;text-align:center;line-height:29px;color:#3a3220}

.brand{display:flex;flex-direction:column;align-items:center;gap:6px}
.brand-mark{width:44px;height:44px;border:1.5px solid currentColor;border-radius:50%}
.brand-name{font-size:11px;letter-spacing:4px;font-weight:500}
.site-brand{left:152px;top:44px;color:var(--ink)}

.main-nav{top:57px;right:232px;display:flex;gap:36px;font-size:12px;font-weight:500;white-space:nowrap}
.nav-icon{top:55px}

.page-title{top:138px;width:1200px;text-align:center;font-size:44px;line-height:52px}
.page-intro{top:192px;left:265px;width:670px;text-align:center;font-size:14.5px;line-height:22px;color:var(--text)}

.story-heading{left:157px;top:320px;font-size:27px;line-height:36px;width:360px}
.story-text{left:157px;top:404px;width:345px;font-size:12px;line-height:20.3px;color:var(--text)}
.story-pattern{left:537px;top:470px;width:267px;height:207px;background:#f2f2f2}
.story-photo{left:563px;top:311px;width:481px;height:339px;background:linear-gradient(135deg,#6b6a63,#d9d6cc 45%,#b5b57a 75%,#8b8a4a)}

.banner-photo{left:0;top:743px;width:1200px;height:359px;background:linear-gradient(90deg,#c98d4f,#e8cfae 30%,#c9b8b6 55%,#b9bfae 80%,#8e9a6a)}
.banner-tab{left:275px;top:1062px;width:650px;height:41px;background:var(--white)}
.natural-heading{top:1110px;width:1200px;text-align:center;font-size:36px;line-height:44px;letter-spacing:.5px}

.feature{top:1210px;width:260px;text-align:center}
.feature svg{display:block;margin:0 auto;overflow:visible}
.feature p{margin-top:20px;font-size:12.5px;line-height:20.5px;color:var(--text)}

.organic{left:0;top:1537px;width:1200px;height:416px;background:var(--soft)}
.organic-label{left:157px;top:1644px;font-size:17px;line-height:24px;color:var(--gold)}
.organic-heading{left:157px;top:1668px;font-size:50px;line-height:58px;letter-spacing:.5px}
.organic-text{left:157px;top:1730px;width:320px;font-size:15px;line-height:20px;color:#444}
.btn-buy{left:154px;top:1805px;width:130px;height:37px;border-radius:19px;background:linear-gradient(90deg,#f2e46a,var(--gold));font-size:11px;font-weight:600;text-align:center;line-height:37px;color:#2a2416}
.product-shot{left:645px;top:1600px;width:425px;height:300px;background:radial-gradient(ellipse at 50% 50%,#3a3a36 0%,#2a2a28 45%,rgba(247,247,247,0) 72%)}

.testimonial{left:0;top:1953px;width:1200px;height:262px;background:linear-gradient(90deg,var(--gold-light),var(--gold-mid) 45%,var(--gold))}
.testimonial-title{top:1996px;width:1200px;text-align:center;font-size:38px;line-height:46px}
.quote-mark{font-family:"Playfair Display",serif;font-size:40px;line-height:0;color:var(--white);vertical-align:-12px;margin-right:4px}
.quote-text{left:340px;top:2055px;width:540px;text-align:center;font-size:12.5px;line-height:18px;color:#2a2416}
.quote-name{top:2132px;width:1200px;text-align:center;font-size:10px;font-weight:600;color:var(--white)}
.quote-nav{left:566px;top:2160px}

.site-footer{left:0;top:2215px;width:1200px;height:305px;background:var(--footer)}
.footer-brand{left:156px;top:2257px;color:var(--gold-mid)}
.footer-text{left:157px;top:2346px;width:320px;font-size:11px;line-height:18px;color:var(--white)}
.social{top:2429px;width:37px;height:37px;border:1px solid #888;border-radius:50%}
.footer-links{left:782px;top:2303px;font-size:13px;line-height:27.8px;color:var(--white)}
.footer-contact{left:911px;top:2303px;font-size:11px;color:#ddd}
.footer-contact h4{font-size:11px;font-weight:500;color:var(--white);margin-bottom:12px}
.contact-row{display:flex;gap:8px;margin-bottom:8px;line-height:16px}
.contact-row svg{flex:none;margin-top:2px}
.copyright{left:0;top:2520px;width:1200px;height:56px;background:#f5f5f5;text-align:center;font-size:9px;line-height:50px;color:#666}
</style>
</head>
<body>

<div class="abs promo-bar">Halcyon Delta 8 Premium Gummies</div>

<header>
  <div class="abs brand site-brand"><span class="brand-mark"></span><span class="brand-name">HALCYON</span></div>
  <nav class="abs main-nav"><span>HOME</span><span>OUR STORY</span><span>SHOP</span><span>CONTACT US</span></nav>
  <svg class="abs nav-icon" style="left:987px" width="18" height="18" viewBox="0 0 18 18" fill="none" stroke="#222" stroke-width="1.6"><circle cx="7.5" cy="7.5" r="5.5"/><path d="M11.5 11.5L16 16"/></svg>
  <svg class="abs nav-icon" style="left:1018px" width="24" height="22" viewBox="0 0 24 22" fill="none" stroke="#222" stroke-width="1.5"><path d="M1 3h3l3 11h11l3-8H6"/><circle cx="9" cy="18" r="1.6"/><circle cx="17" cy="18" r="1.6"/><circle cx="19" cy="3" r="3" fill="#e0b33a" stroke="none"/></svg>
</header>

<h1 class="abs serif page-title">OUR STORY</h1>
<p class="abs page-intro">Lorem ipsum dolor sit amet, consectetur adipiscing elit, sed do eiusmod amet, consectetu ipsum dolor sit amet, consectetur adipiscing elit, sed do eiusmod</p>

<section>
  <h2 class="abs serif story-heading">HALCYON DELTA 8 PREMIUM GUMMIES</h2>
  <p class="abs story-text">Ut wisi enim ad minim veniam, quis nostrud exerci tation ullamcorper suscipit lobortis nisl ut aliquip ex ea commodo consequat. Duis autem vel eum iriure dolor in hendrerit in vulputate velit esse molestie conLorem ipsum dolor sit amet, consectetuer adipiscing elit, sed diam nonummy nibh euismod tincidunt ut laoreet dolore magna aliquam erat volutpat. Ut wisi enim ad minim veniam, quis nostrud exerci tation ullamcorper suscipit lobortis nisl ut aliquip ex ea commodo consequat. Duis autem vel eum iriure dolor in hendrerit in vulputate velit esse molestie consequat.</p>
  <div class="abs story-pattern"></div>
  <div class="abs story-photo" role="img" aria-label="Lab technician in a white coat inspecting hemp plant material on a processing line"></div>
</section>

<section>
  <div class="abs banner-photo" role="img" aria-label="Group of friends dancing with raised arms in a sunlit field"></div>
  <div class="abs banner-tab"></div>
  <h2 class="abs serif natural-heading">WE ALWAYS KEEP IT NATURAL</h2>

  <div class="abs feature" style="left:151px">
    <svg width="150" height="150" viewBox="0 0 150 150">
      <defs><path id="arcA" d="M25.6 119.6 A66 66 0 0 0 124.4 119.6"/></defs>
      <path d="M23 124.6 A70 70 0 1 1 127 124.6" fill="none" stroke="#222" stroke-width="1.5"/>
      <g transform="translate(5,0)">
        <path d="M78 34 l28 10 v22 c0 18-14 30-28 38z" fill="#faf0a8"/>
        <path d="M70 34 l30 10 v22 c0 18-14 30-30 38 c-16-8-30-20-30-38 v-22z" fill="none" stroke="#c9a23e" stroke-width="2.2"/>
        <path d="M70 44 l20 7 v15 c0 12-9 20-20 26 c-11-6-20-14-20-26 v-15z" fill="none" stroke="#c9a23e" stroke-width="2"/>
      </g>
      <text font-family="Poppins,sans-serif" font-size="11" font-weight="500" fill="#333"><textPath href="#arcA" startOffset="50%" text-anchor="middle">1. UTISI WNIM</textPath></text>
    </svg>
    <p>Ut wisi enim ad minim veniam, quis nostrud exerci tation ullamcorper suscipit lobortis nisl ut aliquip ex ea commodo consequat. Duis autem vel eum iriure dolor in hendrerit in vulputate velit esse</p>
  </div>

  <div class="abs feature" style="left:463px">
    <svg width="150" height="150" viewBox="0 0 150 150">
      <defs><path id="arcB" d="M25.6 119.6 A66 66 0 0 0 124.4 119.6"/></defs>
      <path d="M23 124.6 A70 70 0 1 1 127 124.6" fill="none" stroke="#222" stroke-width="1.5"/>
      <path d="M84 38 c14-4 20 2 20 2 c0 22-12 36-24 42z" fill="#faf0a8"/>
      <g fill="none" stroke="#c9a23e" stroke-width="2.2">
        <path d="M75 36 v62"/>
        <path d="M75 51 c-8-2-13-8-14-16 c8 1 13 7 14 16z"/><path d="M75 51 c8-2 13-8 14-16 c-8 1-13 7-14 16z"/>
        <path d="M75 68 c-8-2-13-8-14-16 c8 1 13 7 14 16z"/><path d="M75 68 c8-2 13-8 14-16 c-8 1-13 7-14 16z"/>
        <path d="M75 85 c-8-2-13-8-14-16 c8 1 13 7 14 16z"/><path d="M75 85 c8-2 13-8 14-16 c-8 1-13 7-14 16z"/>
      </g>
      <text font-family="Poppins,sans-serif" font-size="11" font-weight="500" fill="#333"><textPath href="#arcB" startOffset="50%" text-anchor="middle">2. LORIAM IPSAM</textPath></text>
    </svg>
    <p>Loriamd minim veniam, quis nostrud exerci tation ullamcorper suscipit lobortis nisl ut aliquip ex ea commodo consequat. Duis autem vel eum iriure dolor in</p>
  </div>

  <div class="abs feature" style="left:776px">
    <svg width="150" height="150" viewBox="0 0 150 150">
      <defs><path id="arcC" d="M25.6 119.6 A66 66 0 0 0 124.4 119.6"/></defs>
      <path d="M23 124.6 A70 70 0 1 1 127 124.6" fill="none" stroke="#222" stroke-width="1.5"/>
      <circle cx="83" cy="68" r="26" fill="#faf0a8"/>
      <circle cx="75" cy="66" r="25" fill="none" stroke="#c9a23e" stroke-width="8" stroke-dasharray="9.8 9.8"/>
      <circle cx="75" cy="66" r="22" fill="none" stroke="#c9a23e" stroke-width="2.2"/>
      <circle cx="75" cy="66" r="10" fill="none" stroke="#c9a23e" stroke-width="2.2"/>
      <text font-family="Poppins,sans-serif" font-size="11" font-weight="500" fill="#333"><textPath href="#arcC" startOffset="50%" text-anchor="middle">3. AORIAM SAM</textPath></text>
    </svg>
    <p>Ut wisi enim ad minim veniam, quis nostrud exerci tation ullamcorper suscipit lobortis nisl ut aliquip ex ea commodo consequat. Duis autem vel eum iriure dolor in hendrerit</p>
  </div>
</section>

<section>
  <div class="abs organic"></div>
  <div class="abs organic-label">HALCYON DELTA 8 PREMIUM GUMMIES</div>
  <h2 class="abs serif organic-heading">100% ORGANIC</h2>
  <p class="abs organic-text">Lorem ipsum dolor sit amet, consectetur adipiscing elit, sed do eiusmod</p>
  <div class="abs btn-buy">BUY NOW</div>
  <div class="abs product-shot" role="img" aria-label="Two black resealable gummy pouches floating at an angle"></div>
</section>

<section>
  <div class="abs testimonial"></div>
  <h2 class="abs serif testimonial-title">TESTIMONIAL</h2>
  <p class="abs quote-text"><span class="quote-mark">“</span>Duis autem vel eum iriure dolor in hendrerit in vulputate velit esse molestie consequat, vel illum dolore eu feugiat nulla facilisis at vero eros et accumsan et iusto odio dignissim qui blandit praesent luptatum zzril delenit augue duis dolore te feugait nulla facilisi.</p>
  <div class="abs quote-name">LENA PARK, ADIPSING AMET</div>
  <svg class="abs quote-nav" width="90" height="12" viewBox="0 0 90 12" fill="none" stroke="#5a4a20" stroke-width="1.2">
    <path d="M11 6H3M6 3L3 6l3 3"/>
    <circle cx="25" cy="6" r="2.5" fill="#2a2416" stroke="none"/>
    <circle cx="38" cy="6" r="2.2" fill="#8a7640" stroke="none"/>
    <circle cx="50" cy="6" r="2.2" fill="#8a7640" stroke="none"/>
    <circle cx="62" cy="6" r="2.2" fill="#8a7640" stroke="none"/>
    <path d="M77 6h8M82 3l3 3-3 3"/>
  </svg>
</section>

<footer>
  <div class="abs site-footer"></div>
  <div class="abs brand footer-brand"><span class="brand-mark" style="width:52px;height:52px"></span><span class="brand-name">HALCYON</span></div>
  <p class="abs footer-text">Sed diam nonummy nibh euismod tincidunt ut laoreet dolore magna aliquam erat volutpat widsi enim ad minim.</p>
  <span class="abs social" style="left:162px" aria-label="Social profile"></span>
  <span class="abs social" style="left:208px" aria-label="Social profile"></span>
  <span class="abs social" style="left:253px" aria-label="Social profile"></span>
  <div class="abs footer-links"><div>Home</div><div>Our Story</div><div>Shop</div><div>Contact Us</div></div>
  <div class="abs footer-contact">
    <h4>Halcyon Delta 8 Gummies</h4>
    <div class="contact-row"><svg width="11" height="13" viewBox="0 0 11 13" fill="none" stroke="#e0b33a" stroke-width="1.2"><path d="M5.5 12s4.5-4.5 4.5-7.5a4.5 4.5 0 0 0-9 0C1 7.5 5.5 12 5.5 12z"/><circle cx="5.5" cy="4.5" r="1.6"/></svg><span>123 W. Dolor sit amet.<br>Stive road 406 Boise,<br>ID 12345</span></div>
    <div class="contact-row"><svg width="12" height="12" viewBox="0 0 12 12" fill="none" stroke="#e0b33a" stroke-width="1.2"><path d="M2 1h2.5l1 3-1.5 1a7 7 0 0 0 3 3l1-1.5 3 1V10a1 1 0 0 1-1 1C5 11 1 7 1 2a1 1 0 0 1 1-1z"/></svg><span>123-456-7890</span></div>
    <div class="contact-row"><svg width="12" height="10" viewBox="0 0 12 10" fill="none" stroke="#e0b33a" stroke-width="1.2"><rect x="0.6" y="0.6" width="10.8" height="8.8"/><path d="M1 1l5 4.5L11 1"/></svg><span>info@halcyon.com</span></div>
  </div>
  <div class="abs copyright">© 2021 Halcyon</div>
</footer>

</body>
</html>
```